Corvane Capital Business Cards

These are professional business cards that are for my family office.
Put fake emails and phone numbers as of now until I finalize those components. This family office controls my families investments, assets, and future. The cards should be professional.
..
.
.
.
I just uploaded another variation of a logo I would like to see as a business card to I am inbeteen which logo to use

Target Market(s)

business

Industry/Entity Type

business

Contact Information for Business Card

Professional, wealth related, finance related.

Requirements
Must have
• Logo

```html
<!DOCTYPE html>
<html lang="en">
<head>
<meta charset="utf-8">
<title>Corvane Capital Business Cards</title>
<link rel="stylesheet" href="https://fonts.googleapis.com/css2?family=Maven+Pro:wght@400;500&display=swap">
<style>
  :root {
    --backdrop: #8c4f33;
    --card-white: #ffffff;
    --card-shade: #efefef;
    --ink: #111111;
    --grey: #888888;
    --grey-light: #9a9a9a;
    --card-dark: #2a2a2a;
    --card-dark-edge: #3c3c3c;
    --logo-brown: #3e2015;
    --back-text: #7d7d7d;
  }
  * { margin: 0; padding: 0; box-sizing: border-box; }
  html, body { width: 1200px; height: 1051px; overflow: hidden; }
  body { background: var(--backdrop); position: relative; font-family: "Maven Pro", sans-serif; }

  .card { position: absolute; border-radius: 14px; box-shadow: 0 6px 14px rgba(0,0,0,.35); overflow: hidden; }

  .card-front {
    left: 150px; top: 145px; width: 600px; height: 380px;
    background: linear-gradient(100deg, var(--card-shade) 0%, var(--card-white) 30%, var(--card-white) 100%);
  }
  .holder { position: absolute; left: 64px; top: 188px; color: var(--ink); }
  .holder-name { font-size: 27px; font-weight: 500; letter-spacing: .5px; }
  .holder-title { font-size: 16px; margin-top: 1px; }
  .divider { position: absolute; left: 290px; top: 84px; width: 1.5px; height: 246px; background: #333; }
  .company-name {
    position: absolute; left: 355px; top: 86px;
    font-weight: 500; font-size: 20px; color: var(--ink); letter-spacing: 1.5px; text-transform: uppercase;
  }
  .contacts { position: absolute; left: 340px; top: 148px; list-style: none; }
  .contacts li { display: flex; align-items: center; height: 31px; font-size: 13px; color: var(--ink); white-space: nowrap; }
  .contacts svg { width: 24px; height: 24px; margin-right: 10px; flex: none; }
  .dots { position: absolute; left: 16px; bottom: 20px; display: flex; gap: 6px; }
  .dots span { width: 23px; height: 23px; border-radius: 50%; background: var(--grey); }
  .band { position: absolute; left: 156px; right: 0; bottom: 44px; height: 10px; background: var(--grey); }

  .card-back {
    left: 481px; top: 520px; width: 583px; height: 377px;
    background: linear-gradient(100deg, #1f1f1f 0%, var(--card-dark) 55%, var(--card-dark-edge) 100%);
    display: flex; align-items: center; justify-content: center; gap: 16px;
  }
  .back-mark { width: 40px; height: 40px; border: 3px solid var(--back-text); border-radius: 50%; flex: none; }
  .back-name { font-weight: 500; font-size: 28px; color: var(--back-text); letter-spacing: 2px; text-transform: uppercase; }

  .lockup { position: absolute; left: 790px; top: 210px; width: 380px; display: flex; align-items: center; justify-content: center; gap: 14px; }
  .lockup-mark { width: 30px; height: 30px; background: var(--logo-brown); flex: none; }
  .lockup-name { font-weight: 500; font-size: 28px; color: var(--logo-brown); letter-spacing: 2px; text-transform: uppercase; white-space: nowrap; }
</style>
</head>
<body>

<section class="card card-front">
  <div class="holder">
    <p class="holder-name">Ellis Harmon</p>
    <p class="holder-title">Director</p>
  </div>
  <div class="divider"></div>
  <p class="company-name">Corvane Capital</p>
  <ul class="contacts">
    <li>
      <svg viewBox="0 0 24 24"><circle cx="12" cy="12" r="12" fill="var(--grey-light)"/><path d="M8.5 6.5l2 2-1.2 1.5c.8 1.7 2 2.9 3.7 3.7l1.5-1.2 2 2-1.3 1.6c-3.8-.6-7-3.8-7.6-7.6z" fill="#fff"/></svg>
      001 000 0000
    </li>
    <li>
      <svg viewBox="0 0 24 24"><circle cx="12" cy="12" r="12" fill="var(--grey-light)"/><path d="M12 5a4.5 4.5 0 0 0-4.5 4.5C7.5 13 12 19 12 19s4.5-6 4.5-9.5A4.5 4.5 0 0 0 12 5z" fill="#fff"/><circle cx="12" cy="9.5" r="1.7" fill="var(--grey-light)"/></svg>
      New York, United States
    </li>
    <li>
      <svg viewBox="0 0 24 24"><circle cx="12" cy="12" r="12" fill="var(--grey-light)"/><rect x="6" y="8" width="12" height="8.5" fill="none" stroke="#fff" stroke-width="1.2"/><path d="M6 8l6 5 6-5M6 16.5l4.5-4.5M18 16.5l-4.5-4.5" fill="none" stroke="#fff" stroke-width="1.2"/></svg>
      ellisharmon@corvanecapital.com
    </li>
    <li>
      <svg viewBox="0 0 24 24"><circle cx="12" cy="12" r="12" fill="var(--grey-light)"/><g fill="none" stroke="#fff" stroke-width="1.1"><circle cx="12" cy="12" r="6"/><ellipse cx="12" cy="12" rx="2.6" ry="6"/><path d="M6 12h12M7 9h10M7 15h10"/></g></svg>
      www.corvanecapital.com
    </li>
  </ul>
  <div class="dots"><span></span><span></span><span></span><span></span><span></span></div>
  <div class="band"></div>
</section>

<section class="card card-back" role="img" aria-label="Dark card back with a faint repeating pattern of the company name">
  <div class="back-mark"></div>
  <p class="back-name">Corvane Capital</p>
</section>

<section class="lockup">
  <div class="lockup-mark"></div>
  <p class="lockup-name">Corvane Capital</p>
</section>

</body>
</html>
```